KAJU Freightways #ALLKAJU Business Cards & Letterhead

I am looking to business cards designed for our organization. We are currently undergoing a small re-branding that is taking place. Our organization is called KAJU Freightways and we are headquartered in Phoenix, AZ. We primarily provide transportation and logistics services to the Marlow Parcel Bureau who is our largest customer. I would like to see a design that incorporates name, title, contact info, website, and address (this will be different depending on the employee). I would also like to see some color on the business card using our logo colors or a variation. I would like our logo on the back of the business card with the website displayed. The final design should communicate that we are a next generation transportation operate that focuses on being driver-first, customer-centric, innovative, and sustainable.We would also like our #ALLKAJU catch phrase incorporated as well.

Target Market(s)

Transportation & Logistics

Industry/Entity Type

Trucking Company

Contact Information for Business Card

-First and Last Name
-Position Title
-Contact Phone
-Contact Email
-Physical Address

Font styles to use
Serif

Colors

Designer to choose colors to be used in the design.

Requirements
Must have
• -KAJU logo prominently displayed
• -#ALLKAJU catch phrase used
• -Some amount of color, design gradient, etc.
• -Logo on the back with website listed (https://www.kajufreightco.example)

```html
<!DOCTYPE html>
<html lang="en">
<head>
<meta charset="utf-8">
<title>KAJU Freightways Business Card</title>
<link href="https://fonts.googleapis.com/css2?family=Roboto+Slab:wght@400;500;700&display=swap" rel="stylesheet">
<style>
  :root {
    --backdrop: #b5b5b5;
    --card: #f3f3f1;
    --navy-teal: #013747;
    --leaf: #7ab529;
    --white: #ffffff;
  }
  * { box-sizing: border-box; margin: 0; padding: 0; }
  html, body { width: 1200px; height: 576px; overflow: hidden; }
  body {
    background: var(--backdrop);
    font-family: "Roboto Slab", Georgia, serif;
    position: relative;
  }
  .card {
    position: absolute;
    background: var(--card);
    border-radius: 10px;
    overflow: hidden;
    box-shadow: 0 3px 6px rgba(0,0,0,0.25);
  }
  .brand-lockup {
    display: flex; align-items: center; gap: 12px;
  }
  .brand-dot { border-radius: 50%; background: var(--leaf); flex: none; }
  .brand-name {
    font-family: "Roboto Slab", Georgia, serif;
    font-weight: 700;
    line-height: 1;
    letter-spacing: 1px;
  }

  /* Back of card */
  .card-back { left: 82px; top: 139px; width: 484px; height: 293px; }
  .card-back .brand-lockup {
    position: absolute; left: 0; right: 0; top: 108px; justify-content: center;
  }
  .card-back .brand-dot { width: 22px; height: 22px; }
  .card-back .brand-name { font-size: 54px; color: var(--navy-teal); }
  .card-back .tagline {
    position: absolute; left: 0; right: 0; top: 182px; text-align: center;
    font-size: 13px; font-weight: 700; letter-spacing: 3px; color: var(--leaf);
  }
  .card-back .website-row {
    position: absolute; left: 0; right: 0; top: 250px;
    display: flex; align-items: center; justify-content: center; gap: 18px;
  }
  .website-row .accent { width: 42px; height: 4px; }
  .website-row .url {
    font-size: 12px; letter-spacing: 2px; color: var(--navy-teal); font-weight: 500;
  }
  .card-back .footer-bar {
    position: absolute; left: 0; right: 0; bottom: 0; height: 14px; display: flex;
  }
  .footer-bar .dark { flex: 1; background: var(--navy-teal); }
  .footer-bar .green { flex: 1; background: var(--leaf); }

  /* Front of card */
  .card-front { left: 602px; top: 138px; width: 481px; height: 291px; }
  .company-title {
    position: absolute; left: 22px; top: 27px;
    font-size: 19.5px; font-weight: 700; line-height: 26px; color: var(--navy-teal);
  }
  .info-band {
    position: absolute; left: 0; right: 0; top: 95px; height: 147px;
    background: var(--navy-teal);
  }
  .person-name {
    position: absolute; left: 22px; top: 16px;
    font-size: 18px; font-weight: 700; color: var(--leaf);
  }
  .person-role {
    position: absolute; left: 22px; top: 43px;
    font-size: 12px; color: var(--white);
  }
  .contact-list {
    position: absolute; left: 22px; top: 75px; list-style: none;
  }
  .contact-list li {
    display: flex; align-items: center; gap: 13px;
    height: 18.5px; font-size: 12px; color: var(--white);
  }
  .contact-list svg { width: 11px; height: 11px; }
  .info-band .brand-lockup {
    position: absolute; right: 26px; top: 50px;
  }
  .info-band .brand-dot { width: 20px; height: 20px; }
  .info-band .brand-name { font-size: 50px; color: var(--white); }
  .address {
    position: absolute; left: 22px; top: 257px;
    font-size: 12.5px; color: var(--navy-teal);
  }
</style>
</head>
<body>
  <section class="card card-back" aria-label="Business card back">
    <div class="brand-lockup"><span class="brand-dot"></span><span class="brand-name">KAJU</span></div>
    <p class="tagline">#ALLKAJU</p>
    <div class="website-row">
      <svg class="accent" viewBox="0 0 42 4" aria-hidden="true"><polygon points="0,2 42,0 42,4" fill="var(--leaf)"/></svg>
      <span class="url">www.kajufreightco.example</span>
      <svg class="accent" viewBox="0 0 42 4" aria-hidden="true"><polygon points="0,0 42,2 0,4" fill="var(--leaf)"/></svg>
    </div>
    <div class="footer-bar"><span class="dark"></span><span class="green"></span></div>
  </section>

  <section class="card card-front" aria-label="Business card front">
    <h1 class="company-title">KAJU Freightways and<br>Energy Services</h1>
    <div class="info-band">
      <h2 class="person-name">Dorian Halvorsen</h2>
      <p class="person-role">Chairman &amp; CEO</p>
      <ul class="contact-list">
        <li>
          <svg viewBox="0 0 12 12" aria-hidden="true"><path d="M1 4 Q6 0 11 4 L10 5.5 L8 4.8 L8 3.6 Q6 3 4 3.6 L4 4.8 L2 5.5 Z M3 6 H9 L10.5 11 H1.5 Z" fill="var(--leaf)"/></svg>
          623-555-0148
        </li>
        <li>
          <svg viewBox="0 0 12 12" aria-hidden="true"><rect x="0.5" y="2" width="11" height="8" fill="var(--leaf)"/><path d="M0.5 2 L6 7 L11.5 2" stroke="var(--navy-teal)" stroke-width="1.2" fill="none"/></svg>
          dorian@kajufreightco.example
        </li>
        <li>
          <svg viewBox="0 0 12 12" aria-hidden="true"><circle cx="6" cy="6" r="5.3" fill="var(--leaf)"/><path d="M0.7 6 H11.3 M6 0.7 V11.3 M6 0.7 Q2.5 6 6 11.3 M6 0.7 Q9.5 6 6 11.3" stroke="var(--navy-teal)" stroke-width="0.8" fill="none"/></svg>
          www.kajufreightco.example
        </li>
      </ul>
      <div class="brand-lockup"><span class="brand-dot"></span><span class="brand-name">KAJU</span></div>
    </div>
    <p class="address">4120 North Cactus Ridge Road Glendale, AZ 85310</p>
  </section>
</body>
</html>
```